Quenvale Capital LLC

Need Professional Business cards for New Investment Fund

Target Market(s)

High Quality investors

Industry/Entity Type

Financial

Contact Information for Business Card

Phone Number +1 555 284 6190
Name Lukas Varenko
Title Fund Manager
email lv@FundQuenvale.com
Website www.FundQuenvale.com

Colors

Designer to choose colors to be used in the design.

Requirements
Must have
• Must have our Logo and all of the above. Must be made so lettering and loge can be raised

```html
<!DOCTYPE html>
<html lang="en">
<head>
<meta charset="UTF-8">
<title>Quenvale Capital – Business Card</title>
<link href="https://fonts.googleapis.com/css2?family=Arimo:wght@400;700&display=swap" rel="stylesheet">
<style>
  :root {
    --stage: #2c2f33;
    --forest: #465142;
    --leaf: #5bbb45;
    --paper: #ffffff;
    --ink: #3b3f3a;
    --muted: #5a5d5a;
  }
  * { margin: 0; padding: 0; box-sizing: border-box; }
  html, body {
    width: 1200px; height: 1000px; overflow: hidden;
    background: var(--stage);
    font-family: "Arimo", Arial, sans-serif;
  }
  .stage { position: relative; width: 1200px; height: 1000px; }
  .card {
    position: absolute; left: 220px; width: 760px; height: 434px;
    border-radius: 22px; overflow: hidden;
    box-shadow: 0 12px 30px rgba(0,0,0,0.45);
  }
  /* Back side */
  .card-back { top: 46px; background: var(--forest); }
  .card-back .brand {
    position: absolute; left: 0; right: 0; top: 160px;
    display: flex; justify-content: center; align-items: center; gap: 14px;
  }
  .brand-mark { width: 30px; height: 30px; background: var(--leaf); flex: none; }
  .brand-name {
    font-weight: 700; font-size: 44px; letter-spacing: 3px;
    text-transform: uppercase; color: var(--paper); white-space: nowrap;
  }
  .card-back .site {
    position: absolute; left: 0; right: 0; bottom: 64px; text-align: center;
    font-size: 22px; color: var(--paper); letter-spacing: 0.5px;
  }
  .card-back .site .site-name { color: var(--leaf); }

  /* Front side */
  .card-front { top: 520px; background: var(--paper); }
  .name-bar {
    position: absolute; left: 40px; top: 108px; width: 8px; height: 56px;
    background: var(--forest);
  }
  .holder-name {
    position: absolute; left: 62px; top: 104px;
    font-weight: 700; font-size: 32px; color: var(--leaf); white-space: nowrap;
  }
  .holder-title {
    position: absolute; left: 62px; top: 144px;
    font-size: 21px; color: var(--ink);
  }
  .rule {
    position: absolute; left: 40px; top: 196px; width: 680px; height: 2px;
    background: var(--forest);
  }
  .contacts { position: absolute; left: 40px; top: 214px; list-style: none; }
  .contacts li {
    display: flex; align-items: center; gap: 12px;
    height: 32px; font-size: 20px; color: var(--muted);
  }
  .contacts svg { width: 18px; height: 18px; flex: none; }
  .card-front .brand {
    position: absolute; right: 44px; top: 104px;
    display: flex; align-items: center; gap: 10px;
  }
  .card-front .brand-mark { width: 22px; height: 22px; }
  .card-front .brand-name { font-size: 30px; letter-spacing: 2px; color: var(--forest); }
  .wave { position: absolute; left: 0; bottom: 0; width: 760px; height: 434px; }
</style>
</head>
<body>
<main class="stage">

  <section class="card card-back" aria-label="Card back">
    <div class="brand">
      <span class="brand-mark"></span>
      <span class="brand-name">Quenvale</span>
    </div>
    <p class="site">www.<span class="site-name">FundQuenvale</span>.com</p>
  </section>

  <section class="card card-front" aria-label="Card front">
    <svg class="wave" viewBox="0 0 760 434" preserveAspectRatio="none" aria-hidden="true">
      <path d="M0,338 C170,420 330,388 470,392 C600,396 700,422 760,434 L0,434 Z" fill="var(--forest)"/>
      <path d="M0,324 C170,406 330,374 470,378 C600,382 700,402 760,420" fill="none" stroke="var(--leaf)" stroke-width="6"/>
    </svg>

    <span class="name-bar"></span>
    <h1 class="holder-name">Lukas Varenko</h1>
    <p class="holder-title">Fund Manager</p>
    <span class="rule"></span>

    <ul class="contacts">
      <li>
        <svg viewBox="0 0 18 18" aria-hidden="true"><rect x="4.5" y="1.5" width="9" height="15" rx="1.5" fill="none" stroke="var(--leaf)" stroke-width="1.8"/><circle cx="9" cy="13.5" r="1" fill="var(--leaf)"/></svg>
        +1 555 284 6190
      </li>
      <li>
        <svg viewBox="0 0 18 18" aria-hidden="true"><rect x="1.5" y="4" width="15" height="10.5" rx="1" fill="var(--leaf)"/><path d="M2 5 L9 10.5 L16 5" fill="none" stroke="#fff" stroke-width="1.5"/></svg>
        lv@FundQuenvale.com
      </li>
      <li>
        <svg viewBox="0 0 18 18" aria-hidden="true"><circle cx="9" cy="9" r="7.5" fill="var(--leaf)"/><path d="M1.5 9 H16.5 M9 1.5 C5 5 5 13 9 16.5 M9 1.5 C13 5 13 13 9 16.5" fill="none" stroke="#fff" stroke-width="1.1"/></svg>
        www.FundQuenvale.com
      </li>
    </ul>

    <div class="brand">
      <span class="brand-mark"></span>
      <span class="brand-name">Quenvale</span>
    </div>
  </section>

</main>
</body>
</html>
```